VOMRA Pty Ltd Business Card

Looking for a simple yet eye-catching double-sided business card design using my company logo on one side and contact details on the other.

Target Market(s)

Government

Industry/Entity Type

Communication Systems Engineering

Contact Information for Business Card

VOMRA Pty Ltd

Requirements
Nice to have
• Would be great to have a QR code so details can be scanned into contacts

```html
<!DOCTYPE html>
<html lang="en">
<head>
<meta charset="utf-8">
<title>VOMRA Pty Ltd Business Card</title>
<link rel="stylesheet" href="https://fonts.googleapis.com/css2?family=Open+Sans:wght@400;700&display=swap">
<style>
  :root {
    --stage: #222222;
    --card: #37414a;
    --ink: #ffffff;
    --ink-soft: #e9ecee;
    --accent-line: #4a545d;
  }
  * { box-sizing: border-box; margin: 0; padding: 0; }
  html, body { width: 1200px; height: 780px; overflow: hidden; }
  body {
    background: var(--stage);
    font-family: "Open Sans", sans-serif;
    color: var(--ink);
    position: relative;
  }
  .card {
    position: absolute;
    width: 560px;
    height: 320px;
    border-radius: 22px;
    background: var(--card);
    overflow: hidden;
  }
  .card--front { left: 320px; top: 55px; }
  .card--back { left: 320px; top: 405px; }

  .brand { display: flex; align-items: center; gap: 14px; }
  .brand__dot { width: 18px; height: 18px; border-radius: 50%; background: var(--ink); }
  .brand__name { font-weight: 700; letter-spacing: 3px; color: var(--ink); }

  .card--front .brand {
    position: absolute; inset: 0; justify-content: center;
  }
  .card--front .brand__name { font-size: 64px; }
  .card--front .brand__dot { width: 30px; height: 30px; }

  .swoosh { position: absolute; inset: 0; width: 100%; height: 100%; }

  .card--back .brand { position: absolute; left: 36px; top: 44px; }
  .card--back .brand__name { font-size: 38px; }

  .holder {
    position: absolute; right: 44px; top: 30px; text-align: right;
  }
  .holder__name { font-size: 26px; font-weight: 700; line-height: 1.1; }
  .holder__role { font-size: 13px; font-weight: 400; color: var(--ink-soft); }
  .holder-bar {
    position: absolute; right: 18px; top: 26px; width: 12px; height: 50px; background: var(--ink);
  }

  .address {
    position: absolute; left: 38px; top: 132px;
    font-size: 14px; line-height: 1.3; color: var(--ink-soft);
  }
  .contacts {
    position: absolute; left: 38px; top: 190px; list-style: none;
    font-size: 14px; line-height: 1.2; color: var(--ink-soft);
  }
  .contacts li { display: flex; align-items: center; gap: 10px; margin-bottom: 6px; }
  .contacts svg { width: 15px; height: 15px; flex: none; }
</style>
</head>
<body>

<section class="card card--front" aria-label="Card front">
  <div class="brand">
    <span class="brand__dot"></span>
    <span class="brand__name">VOMRA</span>
  </div>
</section>

<section class="card card--back" aria-label="Card back">
  <svg class="swoosh" viewBox="0 0 560 320" preserveAspectRatio="none" aria-hidden="true">
    <path d="M0,320 L0,282 C160,300 270,262 335,178 C385,112 455,88 560,92 L560,320 Z" fill="#ffffff"/>
    <path d="M28,296 C150,296 250,272 312,214" fill="none" stroke="var(--accent-line)" stroke-width="3" stroke-linecap="round"/>
  </svg>

  <div class="brand">
    <span class="brand__dot"></span>
    <span class="brand__name">VOMRA</span>
  </div>

  <div class="holder">
    <p class="holder__name">Daniel Hartley</p>
    <p class="holder__role">Co-Founder</p>
  </div>
  <span class="holder-bar"></span>

  <p class="address">42-44 Marlow Street Eastwood<br>NSW 2122 Australia</p>

  <ul class="contacts">
    <li>
      <svg viewBox="0 0 16 16" aria-hidden="true"><path fill="#fff" d="M3.6 1.5l2.2 2.6-1.3 1.6c.9 2 2.4 3.6 4.4 4.6l1.6-1.4 2.7 2.1-1.2 2.4C6.8 13.6 2.2 9 1.4 3z"/></svg>
      <span>(555) 214-0736</span>
    </li>
    <li>
      <svg viewBox="0 0 16 16" aria-hidden="true"><circle cx="8" cy="8" r="6.5" fill="none" stroke="#fff" stroke-width="1.4"/><ellipse cx="8" cy="8" rx="2.8" ry="6.5" fill="none" stroke="#fff" stroke-width="1.2"/><line x1="1.5" y1="8" x2="14.5" y2="8" stroke="#fff" stroke-width="1.2"/></svg>
      <span>www.vomra.com.au</span>
    </li>
    <li>
      <svg viewBox="0 0 16 16" aria-hidden="true"><rect x="1.5" y="3.5" width="13" height="9" rx="1" fill="none" stroke="#fff" stroke-width="1.4"/><path d="M1.5 4l6.5 5 6.5-5" fill="none" stroke="#fff" stroke-width="1.4"/></svg>
      <span>admin@vomra.com.au</span>
    </li>
  </ul>
</section>

</body>
</html>
```